Vantrel System Web Page Design

This project is to design 6 pages of a web based medical system for clinics, hospitals, drugs suppliers, general items suppliers, insurance company, laboratories and patients (basically all parties which could be involved in).We want the designs of the browser, button, icon and layout are based on Zeltor, which is user friendly, looks professional, simple and neat but with powerful functions. We have uploaded few pictures of another system, please do not copy its design because this is not what we are looking for, the pictures are for you to know the elements should be included in our pages. Vantrel web-base system, design 6 pages1. Login PageShould include the following elements-company id with input field-login id with input field-password with input field2. Main Page (Navigation page)Should include the following elements-Appointment-Consultation-Patient-Drugs inventory -General supplies inventory -Laboratory-Suppliers-Insurance-Reports 3. Appointment PageShould include all the the elements in the respective pictures plus the followings-Daily View, Weekly View, Monthly View buttons4. Consultation PageShould include all the the elements in the respective picture5. Patient Page5.1 General information Should include all the the elements in the respective picture5.2 medical history/lab reportsShould include all the the elements in the respective picture plus the followings-Notify patient button-Share report button.
Updated on 28 Nov:
Please stop using Harbor Suite in your designs which is not the name of our system. We have just rename our system to Vantrel, please take note.
We need the system to look professional not playful, do not use too many colors and playful icons.

```html
<!DOCTYPE html>
<html lang="en">
<head>
<meta charset="utf-8">
<title>Vantrel System – Login</title>
<link rel="stylesheet" href="https://fonts.googleapis.com/css2?family=Arimo:wght@400;700&display=swap">
<style>
  :root {
    --page-bg: #e3e3e3;
    --window-bg: #f4f5f6;
    --titlebar-bg: #ececec;
    --titlebar-border: #d4d4d4;
    --brand-blue: #2f76b8;
    --label-blue: #2a6fb3;
    --text-dark: #1c1c1c;
    --text-footer: #3a3a3a;
    --input-border: #a9a9a9;
    --curve-light: #ffffff;
    --curve-shade: #e6e8ea;
    --dot-red: #ee5b55;
    --dot-yellow: #f2be3a;
    --dot-green: #5fc341;
  }
  * { box-sizing: border-box; margin: 0; padding: 0; }
  html, body {
    width: 1200px; height: 761px; overflow: hidden;
    background: var(--page-bg);
    font-family: "Arimo", Helvetica, Arial, sans-serif;
  }
  .app-window {
    position: absolute; left: 37px; top: 60px;
    width: 1128px; height: 640px;
    background: var(--window-bg);
    border-radius: 6px 6px 2px 2px;
    box-shadow: 0 14px 30px rgba(0,0,0,0.35), 0 0 0 1px rgba(0,0,0,0.08);
    overflow: hidden;
  }
  .titlebar {
    position: relative; height: 31px;
    background: var(--titlebar-bg);
    border-bottom: 1px solid var(--titlebar-border);
    text-align: center; line-height: 31px;
    font-size: 16px; color: #333;
  }
  .traffic-lights { position: absolute; left: 12px; top: 9px; display: flex; gap: 8px; }
  .traffic-lights span { width: 15px; height: 15px; border-radius: 50%; border: 1px solid rgba(0,0,0,0.2); }
  .light-close { background: var(--dot-red); }
  .light-min { background: var(--dot-yellow); }
  .light-max { background: var(--dot-green); }
  .fullscreen-icon { position: absolute; right: 8px; top: 6px; }
  .window-body { position: absolute; left: 0; top: 32px; width: 1128px; height: 608px; }
  .backdrop { position: absolute; inset: 0; }
  .brand-name {
    position: absolute; left: 13px; top: 10px;
    font-size: 35px; color: var(--brand-blue); font-weight: 400;
  }
  .system-emblem { position: absolute; left: 518px; top: 131px; }
  .login-title {
    position: absolute; left: 0; width: 100%; top: 252px;
    text-align: center; font-size: 26px; color: var(--text-dark);
  }
  .login-form { position: absolute; left: 0; top: 374px; width: 100%; }
  .field-row { position: absolute; left: 0; height: 31px; width: 100%; }
  .field-row label {
    position: absolute; right: 694px; top: 6px;
    font-size: 17px; color: var(--label-blue); white-space: nowrap;
  }
  .field-row input {
    position: absolute; left: 446px; top: 0;
    width: 234px; height: 31px;
    border: 1px solid var(--input-border); border-radius: 4px;
    background: #fff; box-shadow: inset 0 1px 2px rgba(0,0,0,0.15);
  }
  .submit-button {
    position: absolute; left: 518px; top: 150px;
    width: 89px; height: 29px;
    border: 1px solid #a3a3a3; border-radius: 5px;
    background: linear-gradient(#ffffff, #ececec);
    font-family: inherit; font-size: 16px; color: #111;
  }
  .window-footer {
    position: absolute; right: 15px; bottom: 16px;
    font-size: 15px; color: var(--text-footer); letter-spacing: 0.3px;
  }
  .window-footer .divider { margin: 0 14px; }
</style>
</head>
<body>
  <div class="app-window">
    <div class="titlebar">
      <div class="traffic-lights"><span class="light-close"></span><span class="light-min"></span><span class="light-max"></span></div>
      Vantrel System
      <svg class="fullscreen-icon" width="20" height="20" viewBox="0 0 20 20" aria-hidden="true">
        <path d="M11 3h6v6M17 3l-6 6M9 17H3v-6M3 17l6-6" fill="none" stroke="#8a8a8a" stroke-width="2"/>
      </svg>
    </div>
    <main class="window-body">
      <svg class="backdrop" width="1128" height="608" viewBox="0 0 1128 608" aria-hidden="true">
        <defs>
          <linearGradient id="sheen" x1="0" y1="0" x2="1" y2="1">
            <stop offset="0" stop-color="#ffffff"/>
            <stop offset="1" stop-color="#eef0f1"/>
          </linearGradient>
        </defs>
        <rect width="1128" height="608" fill="url(#sheen)"/>
        <path d="M300 608 C420 420 640 180 1128 40 L1128 608 Z" fill="var(--curve-shade)" opacity="0.7"/>
        <path d="M620 608 C720 430 900 300 1128 250 L1128 608 Z" fill="var(--curve-light)" opacity="0.6"/>
        <path d="M0 420 C180 400 320 470 420 608 L0 608 Z" fill="var(--curve-shade)" opacity="0.55"/>
      </svg>
      <h1 class="brand-name">Vantrel System</h1>
      <svg class="system-emblem" width="92" height="92" viewBox="0 0 92 92" aria-hidden="true">
        <circle cx="46" cy="46" r="43" fill="none" stroke="var(--brand-blue)" stroke-width="4"/>
      </svg>
      <h2 class="login-title">Login to Vantrel System</h2>
      <form class="login-form">
        <div class="field-row" style="top:0"><label for="company-id">Company ID:</label><input id="company-id" type="text"></div>
        <div class="field-row" style="top:44px"><label for="login-id">Login ID:</label><input id="login-id" type="text"></div>
        <div class="field-row" style="top:88px"><label for="password">Password:</label><input id="password" type="password"></div>
        <button class="submit-button" type="submit">Submit</button>
      </form>
      <footer class="window-footer">Forgot Vantrel System ID or Password?<span class="divider">|</span>Copyright © 2018 Vantrel System. All Rights Reserved.</footer>
    </main>
  </div>
</body>
</html>
```